Construction Company

Design a clutter free business card, it can be double-sided utilizing the logo for VKM Ltd simple with all relevant contact information.

Please also a letterhead design to function for the purposes of invoicing, all mail requirements, with header to be distinctive while the footer ties page together and incorporates all necessary information.

For now, please use generic / dummy text and when a winner is selected, I will disclose the contact information.

Hi Designers! Please read the updated brief which includes the design of a business card and letterhead. Thank you!

```html
<!DOCTYPE html>
<html lang="en">
<head>
<meta charset="utf-8">
<title>VKM Ltd — Business Card</title>
<link href="https://fonts.googleapis.com/css2?family=Oswald:wght@500&family=Roboto:wght@400;500&display=swap" rel="stylesheet">
<style>
  :root {
    --backdrop: #2b2b2b;
    --card: #1a1a1b;
    --brand-blue: #0a36a8;
    --brand-gold: #c9a227;
    --text-light: #f2f2f2;
    --divider: #8a8a8a;
  }
  * { box-sizing: border-box; margin: 0; padding: 0; }
  html, body {
    width: 1200px; height: 901px; overflow: hidden;
    background: var(--backdrop);
    font-family: "Roboto", Arial, sans-serif;
  }
  .stage {
    width: 1200px; height: 901px;
    display: flex; flex-direction: column; align-items: center; justify-content: center;
    gap: 48px;
  }
  .card {
    position: relative;
    width: 640px; height: 366px;
    background: var(--card);
    box-shadow: 0 12px 30px rgba(0,0,0,.45);
    overflow: hidden;
  }
  .card__band {
    position: absolute; left: 0; right: 0; bottom: 0;
    height: 10px; background: var(--brand-blue);
  }

  /* Front */
  .brand {
    position: absolute; left: 0; right: 0; top: 108px;
    display: flex; align-items: center; justify-content: center; gap: 18px;
  }
  .brand__dot {
    width: 26px; height: 26px; border-radius: 50%;
    background: var(--brand-gold);
  }
  .brand__name {
    font-family: "Roboto", Arial, sans-serif;
    font-weight: 500; font-size: 84px; letter-spacing: 2px;
    color: var(--brand-blue); line-height: 1;
  }
  .front__web {
    position: absolute; left: 0; right: 0; bottom: 40px;
    text-align: center; font-size: 17px; letter-spacing: .5px;
    color: var(--text-light);
  }
  .front__web span { color: var(--brand-blue); }

  /* Back */
  .person {
    position: absolute; left: 20px; top: 142px; width: 300px;
    text-align: right;
  }
  .person__name {
    font-family: "Oswald", "Arial Narrow", sans-serif;
    font-weight: 500; font-size: 38px; line-height: 1.05;
    color: var(--brand-blue); text-transform: uppercase;
    white-space: nowrap;
  }
  .person__role { font-size: 20px; color: var(--text-light); margin-top: 2px; }
  .back__divider {
    position: absolute; left: 346px; top: 146px;
    width: 1px; height: 84px; background: var(--divider);
  }
  .contact {
    position: absolute; left: 370px; top: 148px;
    list-style: none; display: flex; flex-direction: column; gap: 7px;
  }
  .contact__item {
    display: flex; align-items: center; gap: 14px;
    font-size: 19px; color: var(--text-light); white-space: nowrap;
  }
  .contact__icon { width: 17px; height: 17px; flex: none; }
  .back__address {
    position: absolute; left: 0; right: 0; bottom: 44px;
    text-align: center; font-size: 20px; color: var(--text-light);
  }
</style>
</head>
<body>
<main class="stage">
  <section class="card card--front" aria-label="Card front">
    <div class="brand">
      <span class="brand__dot"></span>
      <span class="brand__name">VKM Ltd</span>
    </div>
    <p class="front__web">www.<span>yourwebsite</span>.com</p>
    <div class="card__band"></div>
  </section>

  <section class="card card--back" aria-label="Card back">
    <div class="person">
      <h1 class="person__name">Daniel Carter</h1>
      <p class="person__role">Manager</p>
    </div>
    <div class="back__divider"></div>
    <ul class="contact">
      <li class="contact__item">
        <svg class="contact__icon" viewBox="0 0 24 24" fill="none" stroke="#0a36a8" stroke-width="2.2" stroke-linejoin="round"><path d="M5 3h4l2 5-2.5 1.5a11 11 0 0 0 6 6L16 13l5 2v4a2 2 0 0 1-2 2A17 17 0 0 1 3 5a2 2 0 0 1 2-2z"/></svg>
        555-014-2780
      </li>
      <li class="contact__item">
        <svg class="contact__icon" viewBox="0 0 24 24" fill="none" stroke="#0a36a8" stroke-width="2.2"><rect x="2" y="5" width="20" height="14" rx="1"/><path d="M2 6l10 7 10-7"/></svg>
        youremail@mailhost.com
      </li>
      <li class="contact__item">
        <svg class="contact__icon" viewBox="0 0 24 24" fill="none" stroke="#0a36a8" stroke-width="2"><circle cx="12" cy="12" r="10"/><ellipse cx="12" cy="12" rx="4.5" ry="10"/><path d="M2 12h20M4 7h16M4 17h16"/></svg>
        www.yourwebsite.com
      </li>
    </ul>
    <p class="back__address">Your address, city, state, ZIP 0000</p>
    <div class="card__band"></div>
  </section>
</main>
</body>
</html>
```